Need help in designing new business card utilizing our new logo.

BuildMark Solutions works with Construction Business Owners, Managers & IT Professionals to strengthen software usage and increase user productivity.

Our Construction Accounting and Mobile Field Management Software Clients engage with us in the following areas:

New Software Implementations
Software Re-Implementations
Redesigning Software Usage at the User Level
Project Coordination & Management
Continued Software Support

Old tag line:
Weighing Options - Implementing Solutions

www.buildmark-solutions.example

Ridge 4 is a product, but not needed for a new business card.

```html
<!DOCTYPE html>
<html lang="en">
<head>
<meta charset="utf-8">
<title>BuildMark Solutions – Business Card</title>
<link rel="stylesheet" href="https://fonts.googleapis.com/css2?family=Open+Sans:wght@400;600;700&family=Oswald:wght@400&display=swap">
<style>
  :root {
    --stage: #1c1c1e;
    --brand-blue: #0b16a3;
    --ink-blue: #1a1fa8;
    --card-white: #ffffff;
    --text-grey: #3a3a3a;
    --rule-grey: #8a8a8a;
    --logo-grey: #b9b9bb;
    --rule-light: rgba(255,255,255,0.45);
  }
  * { box-sizing: border-box; margin: 0; padding: 0; }
  html, body { width: 1200px; height: 900px; overflow: hidden; }
  body {
    background: var(--stage);
    font-family: "Open Sans", Arial, sans-serif;
    display: flex;
    flex-direction: column;
    align-items: center;
    justify-content: center;
    gap: 56px;
  }
  .card {
    width: 560px;
    height: 320px;
    border-radius: 22px;
    position: relative;
    overflow: hidden;
  }

  /* Back: services */
  .card--back { background: var(--brand-blue); color: var(--card-white); padding: 34px 36px 0; }
  .services {
    list-style: none;
    display: grid;
    grid-template-columns: 1fr 1fr;
    row-gap: 18px;
    column-gap: 20px;
  }
  .service {
    display: flex;
    align-items: center;
    gap: 10px;
    font-family: "Oswald", "Arial Narrow", sans-serif;
    font-size: 13px;
    letter-spacing: 0.2px;
  }
  .service__icon { width: 40px; height: 40px; flex: none; }
  .tagline-band {
    position: absolute;
    left: 36px; right: 36px; bottom: 34px;
    border-top: 1px solid var(--rule-light);
    border-bottom: 1px solid var(--rule-light);
    padding: 14px 0;
    text-align: center;
    font-weight: 600;
    font-size: 17px;
    letter-spacing: 0.3px;
  }

  /* Front: contact */
  .card--front { background: var(--card-white); }
  .brand {
    position: absolute;
    top: 60px; left: 0; right: 0;
    display: flex;
    justify-content: center;
    align-items: center;
    gap: 14px;
  }
  .brand__mark { width: 26px; height: 26px; background: var(--ink-blue); }
  .brand__name {
    font-weight: 700;
    font-size: 30px;
    color: var(--ink-blue);
    letter-spacing: 0.5px;
  }
  .divider {
    position: absolute;
    left: 36px; right: 36px; top: 190px;
    border-top: 1px solid var(--rule-grey);
  }
  .contact-lines {
    position: absolute;
    right: 36px; top: 126px;
    list-style: none;
    text-align: right;
    font-size: 13.5px;
    line-height: 20px;
    color: var(--text-grey);
  }
  .contact-lines li { display: flex; justify-content: flex-end; align-items: center; gap: 7px; }
  .contact-lines svg { width: 11px; height: 11px; fill: var(--ink-blue); }
  .person {
    position: absolute;
    left: 36px; top: 204px;
    color: var(--text-grey);
    font-size: 14px;
    line-height: 19px;
  }
  .person__name { color: var(--ink-blue); font-weight: 600; font-size: 19px; letter-spacing: 0.3px; line-height: 24px; }
  .person__role { margin-bottom: 10px; }
  .person__web span { color: var(--ink-blue); }
</style>
</head>
<body>

<section class="card card--back" aria-label="Card back: services">
  <ul class="services">
    <li class="service"><svg class="service__icon" role="img" aria-label="Software install icon" viewBox="0 0 40 40"><circle cx="20" cy="20" r="20" fill="#fff"/></svg>New Software Implementations</li>
    <li class="service"><svg class="service__icon" role="img" aria-label="Software re-install icon" viewBox="0 0 40 40"><circle cx="20" cy="20" r="20" fill="#fff"/></svg>Software Re-Implementations</li>
    <li class="service"><svg class="service__icon" role="img" aria-label="Redesign cycle icon" viewBox="0 0 40 40"><circle cx="20" cy="20" r="20" fill="#fff"/></svg>Redesigning Software Usage at the User Level</li>
    <li class="service"><svg class="service__icon" role="img" aria-label="Support agent icon" viewBox="0 0 40 40"><circle cx="20" cy="20" r="20" fill="#fff"/></svg>Continued Software Support</li>
    <li class="service"><svg class="service__icon" role="img" aria-label="Project network icon" viewBox="0 0 40 40"><circle cx="20" cy="20" r="20" fill="#fff"/></svg>Project Coordination &amp; Management</li>
  </ul>
  <p class="tagline-band">WEIGHING OPTIONS - IMPLEMENTING SOLUTIONS</p>
</section>

<section class="card card--front" aria-label="Card front: contact details">
  <div class="brand">
    <span class="brand__mark"></span>
    <span class="brand__name">BuildMark Solutions</span>
  </div>

  <ul class="contact-lines">
    <li>044-555 010 200 <svg viewBox="0 0 12 12"><path d="M2 1h3l1 3-2 1a7 7 0 0 0 3 3l1-2 3 1v3c-6 1-10-3-9-9z"/></svg></li>
    <li>044-555 010 200 <svg viewBox="0 0 12 12"><path d="M3 0h6v12H3zM4 1.5v8h4v-8z"/></svg></li>
    <li>info@buildmark-solutions.example <svg viewBox="0 0 12 12"><path d="M0 2h12v8H0zM1 3l5 4 5-4z"/></svg></li>
  </ul>

  <div class="divider"></div>

  <div class="person">
    <p class="person__name">DANIEL HARTLEY</p>
    <p class="person__role">Managing Director</p>
    <p>12345, Address Goes Here</p>
    <p>Country Name, 123456</p>
    <p class="person__web">www.<span>buildmark-solutions</span>.example</p>
  </div>
</section>

</body>
</html>
```